"Velt Rover" Soil Conditioner for Lawn and Garden.

I need a product label with logo for a square 1 qt F Style plastic Bottle. The area would be 3.75" wide x 4.125" Tall front and back panel. Needs plenty of text area on the back panel.

Target Market(s)

Landscape and Garden

Industry/Entity Type

Home and Garden

Requirements
Must have
• Focus on the problems of heavy soils

```html
<!DOCTYPE html>
<html lang="en">
<head>
<meta charset="utf-8">
<title>Velt Rover Soil Conditioner Label</title>
<link href="https://fonts.googleapis.com/css2?family=Bebas+Neue&family=Poppins:wght@400;600;700&display=swap" rel="stylesheet">
<style>
:root{
  --paper:#ffffff;
  --caption:#9a9a9a;
  --leaf:#7ed321;
  --leaf-deep:#5fae16;
  --forest:#1f4a14;
  --forest-dark:#10300b;
  --soil:#262d22;
  --ink:#0d2208;
  --white:#ffffff;
}
*{margin:0;padding:0;box-sizing:border-box}
html,body{width:1200px;height:705px;overflow:hidden;background:var(--paper)}
body{position:relative;font-family:"Poppins",sans-serif;color:var(--white)}
.caption{position:absolute;top:18px;font-family:"Bebas Neue",sans-serif;font-size:24px;letter-spacing:1px;color:var(--caption);width:566px;text-align:center}
.caption.front{left:28px}
.caption.back{left:611px}
.panel{position:absolute;top:56px;width:566px;height:622px;overflow:hidden}
.panel.front{left:28px}
.panel.back{left:611px}
.panel-bg{position:absolute;inset:0;background:
  radial-gradient(ellipse at 50% 25%,rgba(70,110,40,.55),transparent 60%),
  linear-gradient(180deg,var(--forest) 0%,var(--soil) 45%,#2b3528 70%,var(--forest) 100%)}
.abs{position:absolute}
.heading{font-family:"Bebas Neue",sans-serif;line-height:1}
.claim{left:0;width:566px;top:42px;display:flex;justify-content:center;align-items:center;gap:14px}
.claim span{font-family:"Bebas Neue",sans-serif;font-size:36px;color:var(--white);line-height:1}
.brand{left:0;width:566px;text-align:center;font-family:"Bebas Neue",sans-serif;line-height:.8}
.brand.top{top:168px;font-size:150px;color:var(--white)}
.brand.bottom{top:274px;font-size:150px;color:var(--leaf)}
.subtitle{left:0;width:566px;text-align:center;font-family:"Bebas Neue",sans-serif;font-size:36px;line-height:1}
.subtitle.one{top:390px;color:var(--white)}
.subtitle.two{top:420px;color:var(--leaf)}
.tag{position:absolute;background:var(--forest);color:var(--leaf);font-family:"Bebas Neue",sans-serif;font-size:13px;letter-spacing:.5px;padding:2px 9px 0;line-height:14px}
.small-copy{position:absolute;font-size:11.3px;line-height:11.6px}
.rule-v{position:absolute;width:1px;background:rgba(126,211,33,.35)}
.caution{left:381px;top:501px;font-weight:700;font-size:11.3px;line-height:11.8px}
.volume{left:379px;top:538px;width:135px;height:46px;background:var(--forest-dark);display:flex;align-items:center;justify-content:center;font-family:"Bebas Neue",sans-serif;font-size:21px;color:var(--leaf)}
.intro-box{left:36px;top:43px;width:499px;height:96px;background:rgba(16,48,11,.85);border-radius:16px}
.intro-copy{left:55px;top:60px;width:222px;font-size:12.2px;line-height:15.6px;color:#e9f2e4}
.intro-copy strong{font-weight:700;color:var(--white)}
.intro-title{left:319px;top:61px;font-family:"Bebas Neue",sans-serif;font-size:37px;line-height:.82}
.intro-title .green{color:var(--leaf)}
.facts{left:35px;top:170px;width:502px;height:266px;border:3px solid var(--leaf);border-radius:42px;background:linear-gradient(180deg,var(--forest-dark),var(--forest))}
.fact-label{position:absolute;left:25px;width:91px;height:34px;background:var(--leaf);color:var(--ink);font-family:"Bebas Neue",sans-serif;font-size:18px;display:flex;align-items:center;justify-content:center}
.fact-text{position:absolute;left:129px;width:340px;font-size:9.6px;line-height:11.5px}
.fact-text.strong{font-weight:600;font-size:11.3px}
.rule-h{position:absolute;left:32px;width:435px;height:1px;background:rgba(126,211,33,.25)}
.maker-tag{left:51px;top:459px;width:126px;height:33px;background:var(--leaf-deep);font-family:"Bebas Neue",sans-serif;font-size:19px;display:flex;align-items:center;padding-left:9px}
.maker-address{left:60px;top:498px;font-size:12.2px;line-height:15px}
.maker-phone{left:60px;top:556px;display:flex;align-items:center;gap:8px;font-weight:700;font-size:15px;color:var(--leaf);letter-spacing:.5px}
.origin-badge{left:325px;top:454px;width:48px;height:41px;background:var(--white);border-radius:4px;border:2px solid var(--forest-dark)}
.eco-badge{left:385px;top:455px;width:37px;height:37px;border-radius:50%;background:var(--leaf)}
</style>
</head>
<body>
  <div class="caption front">Front</div>
  <div class="caption back">Back</div>

  <section class="panel front">
    <div class="panel-bg" role="img" aria-label="Close-up photo of dark garden soil with blurred green foliage"></div>

    <div class="abs claim">
      <svg width="38" height="38" viewBox="0 0 38 38" aria-hidden="true">
        <circle cx="19" cy="19" r="16" fill="none" stroke="#7ed321" stroke-width="4"/>
        <path d="M10 19 L17 26 L33 7" fill="none" stroke="#7ed321" stroke-width="5" stroke-linecap="round" stroke-linejoin="round"/>
      </svg>
      <span>100% Effective</span>
    </div>

    <h1 class="abs brand top">Velt</h1>
    <div class="abs brand bottom">Rover</div>

    <div class="abs subtitle one">Soil Conditioner For</div>
    <div class="abs subtitle two">Landscape And Garden:</div>

    <div class="tag" style="left:47px;top:484px">Usages:</div>
    <p class="small-copy" style="left:46px;top:502px;width:260px">Promotes soil drainage and alleviates puddling and dry spots by opening more pore space for water and air on contact.</p>
    <div class="tag" style="left:47px;top:541px">Instruction:</div>
    <p class="small-copy" style="left:49px;top:561px;width:260px">Lightly apply 1 oz./gal of water with a hose end sprayer, and then water in.</p>

    <div class="rule-v" style="left:337px;top:505px;height:67px"></div>

    <div class="tag" style="left:381px;top:484px">Caution:</div>
    <p class="abs caution">KEEP OUT OF REACH<br>OF CHILDREN!</p>
    <div class="abs volume">1 Quart (32 FL.OZ.)</div>
  </section>

  <section class="panel back">
    <div class="panel-bg" role="img" aria-label="Close-up photo of dark garden soil with blurred green foliage"></div>

    <div class="abs intro-box"></div>
    <p class="abs intro-copy">Velt Rover promotes the formation of water stable aggregates aerating and loosening compacted soil. <strong>Not a wetting agent.</strong></p>
    <div class="rule-v" style="left:292px;top:53px;height:76px"></div>
    <h2 class="abs intro-title">Concentrated<br><span class="green">Soil Conditioner</span></h2>

    <div class="abs facts">
      <div class="fact-label" style="top:25px">Application:</div>
      <p class="fact-text" style="top:19px">Best results using a hose end sprayer set at 1 oz./gal of water and lightly apply. Water back for at least 20 minutes. Hand sprayer can be used with the same dosage using sufficient liquid to cover the desired area. Caution, smooth paved surfaces may become slippery. Rinse with water.</p>
      <div class="rule-h" style="top:77px"></div>
      <div class="fact-label" style="top:93px">Benefits:</div>
      <p class="fact-text" style="top:95px">Improves water infiltration, aeration in the root zone, movement of nutrients through the soil profile promoting conditions for plants to thrive. Lessens dry spots, runoff and erosion on slopes.</p>
      <div class="rule-h" style="top:141px"></div>
      <div class="fact-label" style="top:153px">Uses:</div>
      <p class="fact-text strong" style="top:164px;width:360px">New or established lawns, Tree Planting, Garden Beds, Slopes.</p>
      <div class="rule-h" style="top:198px"></div>
      <div class="fact-label" style="top:214px">Ingredients:</div>
      <p class="fact-text strong" style="top:224px;left:130px">Proprietary "Velt Rover" .25% v/v</p>
    </div>

    <div class="abs maker-tag">Manufactured By:</div>
    <p class="abs maker-address">Marrow Creek LLC<br>2218 Alder Crest Rd<br>Fernvale, CA 90210</p>
    <div class="abs maker-phone">
      <svg width="16" height="16" viewBox="0 0 24 24" aria-hidden="true"><path fill="#7ed321" d="M6.6 10.8a15.1 15.1 0 0 0 6.6 6.6l2.2-2.2a1 1 0 0 1 1-.25 11.4 11.4 0 0 0 3.6.57 1 1 0 0 1 1 1V20a1 1 0 0 1-1 1A17 17 0 0 1 3 4a1 1 0 0 1 1-1h3.5a1 1 0 0 1 1 1c0 1.25.2 2.45.57 3.57a1 1 0 0 1-.25 1z"/></svg>
      <span>555-014-2270</span>
    </div>
    <div class="rule-v" style="left:252px;top:477px;height:77px"></div>

    <div class="abs origin-badge"></div>
    <div class="abs eco-badge"></div>
  </section>
</body>
</html>
```